A modern, fresh introduction to Buddhism

I need a book cover for an A6 sized book to be used both for ebook and hard copy. The author is a young, modern Buddhist teacher of high standing who has written this short intro to Buddhism in an informal Q & As format using modern, accessible language to convey profound and meaningful ideas to the general public. The author is Tibetan, but teaches worldwide and is very personable and dynamic. The cover should portray this and have a fresh yet authentic feel to it (nothing new-agey!). Please see the author's websites www.torvenmalsiteacher.org and www.vrmq.org for reference, but do not feel that the design must align completely with the website designs.

Target Market(s)

General public both in Europe and America and in Asia ranging from teenagers to the elderly. A really broad audience.

Industry/Entity Type

Teacher

Requirements
Must have
• Please include the following text that on the front cover:

A Window Onto Stillwaters

By Dorwel Tamsung Geshela

Please include the following on the back cover:

Mirun Teskavo Publications (with attached logo above it)
Nice to have
• A simplistic, artistic, and modern look without any traditional religious images.
Should not have
• No buddha images or religious images. I would prefer a more simplistic, modern and artistic look.

```html
<!DOCTYPE html>
<html lang="en">
<head>
<meta charset="utf-8">
<title>A Window Onto Stillwaters</title>
<link href="https://fonts.googleapis.com/css2?family=Libre+Baskerville:wght@700&family=Marcellus&display=swap" rel="stylesheet">
<style>
  :root {
    --paper: #ffffff;
    --ink: #111111;
    --saffron: #e0862c;
    --smoke-orange: #f0a968;
    --smoke-amber: #f3c77a;
    --smoke-yellow: #e6e66a;
    --smoke-lime: #d9e24f;
  }
  * { margin: 0; padding: 0; box-sizing: border-box; }
  html, body {
    width: 848px;
    height: 1200px;
    overflow: hidden;
    background: var(--paper);
  }
  .cover {
    position: relative;
    width: 848px;
    height: 1200px;
    background: var(--paper);
    overflow: hidden;
  }
  .smoke-art-top {
    position: absolute;
    left: 0;
    top: 0;
    width: 848px;
    height: 693px;
    background:
      radial-gradient(ellipse at 20% 20%, rgba(240,169,104,0.85), rgba(240,169,104,0) 55%),
      radial-gradient(ellipse at 80% 75%, rgba(217,226,79,0.9), rgba(217,226,79,0) 55%),
      linear-gradient(135deg, var(--smoke-orange) 0%, var(--smoke-amber) 45%, var(--smoke-yellow) 100%);
    opacity: 0.75;
  }
  .smoke-art-bottom {
    position: absolute;
    left: 212px;
    top: 1027px;
    width: 636px;
    height: 173px;
    background: linear-gradient(100deg, var(--smoke-yellow) 0%, var(--smoke-amber) 55%, var(--smoke-orange) 100%);
    opacity: 0.7;
  }
  .author {
    position: absolute;
    top: 712px;
    left: 0;
    width: 848px;
    text-align: center;
    font-family: "Marcellus", serif;
    font-size: 25px;
    color: var(--ink);
  }
  .rule {
    position: absolute;
    left: 64px;
    width: 724px;
    height: 2px;
    background: var(--ink);
  }
  .rule-upper { top: 760px; }
  .rule-lower { top: 979px; }
  .title {
    position: absolute;
    top: 826px;
    left: 0;
    width: 848px;
    text-align: center;
    font-family: "Libre Baskerville", serif;
    font-weight: 700;
    font-size: 32px;
    letter-spacing: 0.5px;
    color: var(--ink);
  }
  .subtitle {
    position: absolute;
    top: 886px;
    left: 0;
    width: 848px;
    text-align: center;
    font-family: "Marcellus", serif;
    font-size: 29px;
    color: var(--saffron);
  }
</style>
</head>
<body>
  <main class="cover">
    <div class="smoke-art-top" role="img" aria-label="Flowing wisps of orange and yellow smoke on white"></div>
    <p class="author">Dorwel Tamsung Geshela</p>
    <div class="rule rule-upper"></div>
    <h1 class="title">A WINDOW ONTO STILLWATERS</h1>
    <p class="subtitle">A Short Introduction to the Buddha's Teaching</p>
    <div class="rule rule-lower"></div>
    <div class="smoke-art-bottom" role="img" aria-label="Trailing wisps of yellow and amber smoke"></div>
  </main>
</body>
</html>
```